Design a product reviews website

We need a website design and simple logo for the brand Venlotix.com. The website will provide reviews of technology products and services. The brand and website should be approachable but should also be trustworthy and high quality. The deliverable should be designs, specs and assets that I can provide to a development team to build the website.

Target Market(s)

People researching products to buy.

Industry/Entity Type

Product

Logo Text

Venlotix.com

Number of Pages Required

5+ page

Font styles to use
Sans Serif

Colors
0492cd
0355a3
3176b5
33a6d7
85cae6
85abd2
cedeed
cee9f5

Requirements
Must have
• - Designs for the Homepage, Category and Article pages.
• - Designs for web and mobile.
• - Designs details for the engineering team to use for development.
• - I'm open to other colors than the preferences I chose but I'm more likely to like blues, greys and blacks.

```html
<!DOCTYPE html>
<html lang="en">
<head>
<meta charset="utf-8">
<title>Venlotix.com — Product &amp; Service Reviews</title>
<link href="https://fonts.googleapis.com/css2?family=Open+Sans:wght@400;600;700&display=swap" rel="stylesheet">
<style>
:root{
  --blue:#2fa3d8;
  --blue-dark:#0355a3;
  --ink:#333;
  --muted:#666;
  --line:#e3e3e3;
  --soft:#f6f6f6;
  --star:#f3a81c;
  --hero-a:#2a2a2a;
  --hero-b:#0d0d0d;
  --white:#fff;
}
*{box-sizing:border-box;margin:0;padding:0}
html,body{width:1200px;height:2808px;overflow:hidden}
body{font-family:'Open Sans',sans-serif;color:var(--ink);background:var(--white);position:relative}
.abs{position:absolute}

/* header */
.site-header{left:0;top:0;width:1200px;height:66px;background:var(--soft)}
.menu-btn{left:196px;top:18px;width:32px;height:30px;background:var(--white);display:flex;flex-direction:column;justify-content:center;align-items:center;gap:3px}
.menu-btn span{display:block;width:13px;height:2px;background:var(--blue-dark)}
.brand{font-size:20px;font-weight:600;color:#222;line-height:30px;white-space:nowrap}
.site-header .brand{left:298px;top:18px}
.search{left:449px;top:19px;width:320px;height:26px;display:flex;border:1px solid var(--line);background:var(--white)}
.search input{flex:1;min-width:0;border:0;outline:0;font:inherit}
.search button{width:76px;border:0;background:var(--blue);color:var(--white);font:700 10px 'Open Sans',sans-serif;letter-spacing:.5px}

/* hero */
.hero{left:0;top:66px;width:1200px;height:411px;background:radial-gradient(ellipse at 50% 40%,#3a3a3a 0%,var(--hero-a) 45%,var(--hero-b) 100%);text-align:center}
.hero h1{position:absolute;top:142px;width:100%;font-weight:400;font-size:41px;color:var(--blue)}
.hero p{position:absolute;top:194px;width:100%;font-size:27px;color:var(--white)}
.hero .cta{position:absolute;left:483px;top:252px;width:232px;height:34px;background:var(--blue);color:var(--white);font-weight:700;font-size:16px;line-height:34px;letter-spacing:.5px}
.dots{position:absolute;top:366px;left:0;width:100%;display:flex;justify-content:center;gap:14px}
.dots i{width:9px;height:9px;border-radius:50%;background:var(--white)}
.dots i.on{background:var(--blue)}

.col-title{font-size:13px;font-weight:700;color:#222;top:540px}

/* categories */
.categories{left:189px;top:584px;width:197px;border:1px solid var(--line);list-style:none;box-shadow:0 1px 2px rgba(0,0,0,.06)}
.categories li{height:45px;line-height:45px;padding-left:18px;font-size:13px;color:var(--muted);border-top:1px solid var(--line)}
.categories li.active{background:var(--blue);color:var(--white);border-top:0;height:58px;line-height:58px}

/* featured */
.media{background:linear-gradient(160deg,#d8d8d8,#9a9a9a)}
.feature{left:404px;width:390px}
.feature .media{height:277px;position:relative;border:1px solid var(--line)}
.tags{position:absolute;right:6px;bottom:6px;display:flex;gap:4px}
.tag{background:var(--blue);color:var(--white);font-size:11px;padding:0 12px;height:26px;line-height:26px;white-space:nowrap}
.excerpt{font-size:11px;line-height:20px;color:#555;margin-top:17px}
.byline{display:flex;align-items:center;margin-top:14px;height:42px}
.avatar{width:40px;height:40px;background:linear-gradient(#cfd6dc,#8e9aa5);border:1px solid var(--line)}
.byline .name{margin-left:14px;font-size:14px;font-weight:600}
.byline .meta{margin-left:auto;text-align:right;font-size:14px;font-weight:600}
.stars{color:var(--star);font-size:11px;letter-spacing:-1px;line-height:12px}

.card{width:187px}
.card .media{height:156px;position:relative;border:1px solid var(--line);background:linear-gradient(160deg,#fafafa,#dcdcdc)}
.card .stars{position:absolute;left:6px;bottom:12px}
.card .tag{position:absolute;right:6px;bottom:6px}
.card p{font-size:11px;line-height:19px;color:#555;margin-top:12px}

/* popular */
.pop{left:812px;width:189px}
.pop .media{height:157px;border:1px solid var(--line)}
.pop p{font-size:11px;line-height:19px;color:#555;margin-top:12px}

/* pagination */
.pager{left:404px;top:2415px;display:flex;gap:9px;align-items:center}
.pager a{width:20px;height:20px;border:1px solid #ccc;font-size:9px;line-height:18px;text-align:center;color:#555;text-decoration:none}
.pager a.wide{width:24px}
.pager a.on{background:#333;color:var(--white);border-color:#333}
.pager .gap{width:16px;border-bottom:1px solid #bbb;height:12px}

/* footer */
.site-footer{left:0;top:2497px;width:1200px;height:311px;background:var(--soft);border-top:1px solid var(--line)}
.site-footer .brand{left:240px;top:40px}
.links{top:60px;list-style:none}
.links li{font-size:11px;line-height:22.5px;color:#444;white-space:nowrap}
.legal{left:202px;top:272px;font-size:11px;color:#333}
.payments{left:480px;top:272px;display:flex;align-items:center;gap:10px;font-size:11px}
.payments .card-shape{width:22px;height:13px;border-radius:2px}
.social{left:800px;top:268px;display:flex;align-items:center;gap:4px;font-size:11px}
.social .circ{width:20px;height:20px;border-radius:50%;border:1px solid #4a7fc1}
.lang{left:1172px;top:272px;font-size:11px}
</style>
</head>
<body>

<header class="site-header abs">
  <div class="menu-btn abs"><span></span><span></span><span></span></div>
  <div class="brand abs">Venlotix.com</div>
  <form class="search abs"><input type="text" aria-label="Search"><button type="button">SEARCH</button></form>
</header>

<section class="hero abs" role="img" aria-label="Close-up of a dark speaker grille">
  <h1>Venlotix.com</h1>
  <p>The best product &amp; service reviews and Rankings</p>
  <div class="cta">REVIEW YOUR PRODUCT</div>
  <div class="dots"><i class="on"></i><i></i><i></i><i></i></div>
</section>

<h2 class="col-title abs" style="left:187px">CATEGORIES</h2>
<h2 class="col-title abs" style="left:404px">FEATURED PRODUCTS</h2>
<h2 class="col-title abs" style="left:813px">POPULAR</h2>

<ul class="categories abs">
  <li class="active">Home</li><li>Appliances</li><li>Electronics</li><li>Home Security</li><li>Mobile</li><li>Smart Home</li><li>Software</li>
</ul>

<article class="feature abs" style="top:584px">
  <div class="media" role="img" aria-label="Speaker set with subwoofer on grey backdrop" style="background:linear-gradient(160deg,#b5b5b5,#4a4a4a)">
    <div class="tags"><span class="tag">Home</span><span class="tag">Speakers</span></div>
  </div>
  <p class="excerpt">Lorem Ipsum is simply dummy text of the printing and typesetting industry.<br>Neque porro quisquam est qui dolorem ipsum...</p>
  <div class="byline"><div class="avatar" role="img" aria-label="Author portrait"></div><span class="name">Daniel Reyes</span><div class="meta"><div class="stars">★★★★★</div>July 18,2016</div></div>
</article>

<article class="card abs" style="left:404px;top:1016px"><div class="media" role="img" aria-label="Flat screen television"><span class="stars">★★★★★</span><span class="tag">Mobile</span></div><p>Lorem Ipsum is simply dummy text of the printing</p></article>
<article class="card abs" style="left:607px;top:1016px"><div class="media" role="img" aria-label="Steel refrigerator"><span class="stars">★★★★★</span><span class="tag">Smart Home</span></div><p>Lorem Ipsum is simply dummy text of the printing</p></article>
<article class="card abs" style="left:404px;top:1252px"><div class="media" role="img" aria-label="Washing machine"><span class="stars">★★★★★</span><span class="tag">Mobile</span></div><p>Lorem Ipsum is simply dummy text of the printing</p></article>
<article class="card abs" style="left:607px;top:1252px"><div class="media" role="img" aria-label="Car subwoofer speaker" style="background:linear-gradient(160deg,#e9f3f8,#8fb7cc)"><span class="stars">★★★★★</span><span class="tag">Smart Home</span></div><p>Lorem Ipsum is simply dummy text of the printing</p></article>

<article class="feature abs" style="top:1492px">
  <div class="media" role="img" aria-label="Square black speaker on light backdrop" style="background:linear-gradient(160deg,#e6e6e6,#9a9a9a)">
    <div class="tags"><span class="tag">Home</span><span class="tag">Speakers</span></div>
  </div>
  <p class="excerpt">Lorem Ipsum is simply dummy text of the printing and typesetting industry.<br>Neque porro quisquam est qui dolorem ipsum...</p>
  <div class="byline"><div class="avatar" role="img" aria-label="Author portrait"></div><span class="name">Daniel Reyes</span><div class="meta"><div class="stars">★★★★★</div>July 18,2016</div></div>
</article>

<article class="card abs" style="left:404px;top:1941px"><div class="media" role="img" aria-label="Round black speaker"><span class="stars">★★★★★</span><span class="tag">Mobile</span></div><p>Lorem Ipsum is simply dummy text of the printing</p></article>
<article class="card abs" style="left:607px;top:1941px"><div class="media" role="img" aria-label="Washing machine"><span class="stars">★★★★★</span><span class="tag">Smart Home</span></div><p>Lorem Ipsum is simply dummy text of the printing</p></article>
<article class="card abs" style="left:404px;top:2177px"><div class="media" role="img" aria-label="Security camera"><span class="stars">★★★★★</span><span class="tag">Mobile</span></div><p>Lorem Ipsum is simply dummy text of the printing</p></article>
<article class="card abs" style="left:607px;top:2177px"><div class="media" role="img" aria-label="Portable white speaker" style="background:linear-gradient(160deg,#f0f0f0,#c9c9c9)"><span class="stars">★★★★★</span><span class="tag">Smart Home</span></div><p>Lorem Ipsum is simply dummy text of the printing</p></article>

<nav class="pager abs">
  <a>&lsaquo;</a><a>1</a><a>2</a><a>3</a><a class="on">4</a><a>5</a><span class="gap"></span><a class="wide">15</a><a class="wide">30</a><a class="wide">45</a><a>&rsaquo;</a>
</nav>

<article class="pop abs" style="top:584px"><div class="media" role="img" aria-label="Door access keypad on wall" style="background:linear-gradient(160deg,#cde7ea,#7f9ea6)"></div><p>Lorem Ipsum is simply dummy text of the printing</p></article>
<article class="pop abs" style="top:807px"><div class="media" role="img" aria-label="Steel refrigerator" style="background:linear-gradient(160deg,#fafafa,#cfcfcf)"></div><p>Lorem Ipsum is simply dummy text of the printing</p></article>
<article class="pop abs" style="top:1045px"><div class="media" role="img" aria-label="Security camera" style="background:linear-gradient(160deg,#f5f5f5,#c4c4c4)"></div><p>Lorem Ipsum is simply dummy text of the printing</p></article>
<article class="pop abs" style="top:1269px"><div class="media" role="img" aria-label="Tablet showing smart home controls" style="background:linear-gradient(160deg,#c9a98a,#5d7e9a)"></div><p>Lorem Ipsum is simply dummy text of the printing</p></article>

<footer class="site-footer abs">
  <div class="brand abs">Venlotix.com</div>
  <ul class="links abs" style="left:404px"><li>Home</li><li>Appliances</li><li>Electronics</li><li>Home Security</li><li>Mobile</li><li>Smart Home</li><li>Software</li></ul>
  <ul class="links abs" style="left:537px"><li>Terms Of Use</li><li>Privacy Policy</li><li>Help</li><li>Cookies</li></ul>
  <ul class="links abs" style="left:680px"><li>Payments</li><li>Shipping</li><li>Cancellation &amp; Returns</li><li>FAQ</li><li>Report Infringement</li></ul>
  <ul class="links abs" style="left:814px"><li>Online Shopping</li><li>Affiliate Program</li></ul>
  <div class="legal abs">© 2016 Company Name | All Rights Reserved</div>
  <div class="payments abs">Payment Options
    <span class="card-shape" style="background:#6aa9d8"></span><span class="card-shape" style="background:#2c4fa3"></span><span class="card-shape" style="background:#e0523a"></span><span class="card-shape" style="background:#8fb3de"></span><span class="card-shape" style="background:#c9c9c9"></span>
  </div>
  <div class="social abs">Connect With Us&nbsp;<span class="circ"></span><span class="circ"></span><span class="circ"></span><span class="circ" style="border-color:#d9534f"></span><span class="circ" style="border-color:#d9534f"></span></div>
  <div class="lang abs">CS</div>
</footer>

</body>
</html>
```